Real Estate - Property Management Prospectus/Brochure

We need a prospectus made up, around 9-10 pages including the cover page pages 3 onwards can be all a similar template happy for the front cover to have lots of black. I would like it to look very classy and futuristic, high end, blacks, silvers and whites, i am specializing in managing high end rental properties. i would like to design to correspond with the logo. I need to be able to email this booklet mostly - and also be able to print and mail out as well. I would like it crisp and clean as well - not to much on a page. Please note - happy for the cover to be simple with the logo added - prefer lots of black and with the other pages - they can all be a similar layout template to make this job easier? My website is www.leasemeridian.com.au and phone is 0418 293 547 email is tmarsh@leasemeridian.com.au
Target Market(s)
Investors
Industry/Entity Type
Real Estate
Requirements
Should not have
- Bright greens or bold colours

```html
<!DOCTYPE html>
<html lang="en">
<head>
<meta charset="utf-8">
<title>Principal/Director – LeaseMeridian</title>
<link rel="stylesheet" href="https://fonts.googleapis.com/css2?family=PT+Sans+Narrow:wght@400;700&display=swap">
<style>
  :root {
    --page-top: #0b0b0b;
    --page-bottom: #262626;
    --text-white: #f4f4f4;
    --text-body: #e6e6e6;
    --brand-grey: #8c8c8c;
    --gold: #c39a4b;
    --gold-ink: #1a1408;
    --skyline-top: #232323;
    --skyline-bottom: #3a3a3a;
  }
  * { margin: 0; padding: 0; box-sizing: border-box; }
  html, body { width: 848px; height: 1200px; overflow: hidden; background: var(--page-top); }
  .page {
    position: relative;
    width: 848px;
    height: 1200px;
    overflow: hidden;
    background: linear-gradient(180deg, var(--page-top) 0%, #151515 45%, var(--page-bottom) 100%);
    font-family: "PT Sans Narrow", "Arial Narrow", sans-serif;
    color: var(--text-white);
  }
  .brand {
    position: absolute;
    top: 50px;
    right: 28px;
    width: 216px;
    text-align: center;
    font-size: 20px;
    letter-spacing: 5px;
    color: var(--brand-grey);
  }
  .page-title {
    position: absolute;
    left: 96px;
    top: 142px;
    font-size: 48px;
    font-weight: 400;
    letter-spacing: 0.2px;
  }
  .portrait-slot {
    position: absolute;
    left: 97px;
    top: 263px;
    width: 158px;
    height: 158px;
    border-radius: 50%;
    background: var(--gold);
    color: var(--gold-ink);
    display: flex;
    flex-direction: column;
    align-items: center;
    justify-content: center;
    font-size: 30px;
    line-height: 1.4;
  }
  .bio {
    position: absolute;
    left: 97px;
    top: 480px;
    width: 680px;
    font-size: 19.5px;
    line-height: 34px;
    color: var(--text-body);
    letter-spacing: -0.2px;
  }
  .bio p + p { margin-top: 34px; }
  .skyline {
    position: absolute;
    left: 0;
    bottom: 0;
    width: 848px;
    height: 170px;
    background: linear-gradient(180deg, var(--skyline-top) 0%, var(--skyline-bottom) 100%);
    -webkit-mask: linear-gradient(180deg, transparent 0%, #000 35%);
            mask: linear-gradient(180deg, transparent 0%, #000 35%);
  }
</style>
</head>
<body>
  <main class="page">
    <div class="brand">LEASEMERIDIAN</div>

    <h1 class="page-title">Principal/Director</h1>

    <div class="portrait-slot" role="img" aria-label="Portrait placeholder for Tessa">
      <span>Tessa</span>
      <span>PHOTO</span>
    </div>

    <section class="bio">
      <p>Tessa is an industry expert with a history of excellence in property management, with over 12 years experience and a track record of success.</p>
      <p>Tessa approaches her career with intensity, originality and enthusiasm.<br>Her forward-thinking, innovative attitude offers clients a professional, efficient and a friendly management experience.</p>
    </section>

    <div class="skyline" role="img" aria-label="Dark city skyline silhouette with lit windows along the bottom of the page"></div>
  </main>
</body>
</html>
```